Industrial Project Sign

We need an eye catching (but professional) industrial project sign that will be very large (roughly 12' high x 18' wide). This sign will be highly visible from the adjacent high speed highway.

* The following needs to be at the bottom of the signage: Logo (uploaded), Name (Brightline Property Partners, Inc.) (uploaded) and phone number (415)736-2958

*Name of Project - "Meridale Commerce Park"

* Text items
Land for Sale
Build to Suit
Zoning: Industrial (G I & L I)

* Interesting background that is eye catching
Updates

Good morning all,

We are considering all designers options as we go and are waiting for the final designs to come in by the 4th so that we can give each one a good look.   If you have any new designs, questions, further design options or any tweeks you want to do to current designs, please do so at this time.

Thanks to all of you for your submissions.

Industry/Entity Type

Industrial

```html
<!DOCTYPE html>
<html lang="en">
<head>
<meta charset="utf-8">
<title>Meridale Commerce Park – Land for Sale</title>
<link rel="stylesheet" href="https://fonts.googleapis.com/css2?family=Anton&family=Arimo:wght@700&display=swap">
<style>
  :root {
    --sign-maroon: #3a0000;
    --sign-white: #ffffff;
    --page-bg: #ffffff;
  }
  html, body {
    margin: 0;
    padding: 0;
    width: 1200px;
    height: 1000px;
    overflow: hidden;
    background: var(--page-bg);
  }
  .sign-canvas {
    display: block;
    width: 1200px;
    height: 1000px;
  }
  .sign-panel { fill: var(--sign-maroon); }
  .brand-oval { fill: var(--sign-white); }
  .project-name {
    font-family: "Anton", "Impact", sans-serif;
    font-size: 32px;
    fill: var(--sign-maroon);
  }
  .brand-square { fill: var(--sign-maroon); }
  .brand-name {
    font-family: "Arimo", Arial, sans-serif;
    font-weight: 700;
    font-size: 21px;
    fill: var(--sign-maroon);
  }
  .brand-rule { stroke: var(--sign-maroon); stroke-width: 3; }
  .headline, .zoning-line {
    font-family: "Anton", "Impact", sans-serif;
    fill: var(--sign-white);
  }
  .headline { font-size: 112px; }
  .zoning-line { font-size: 61px; }
  .offer-line {
    font-family: "Arimo", Arial, sans-serif;
    font-weight: 700;
    font-size: 42px;
    fill: var(--sign-white);
  }
  .phone-band { fill: var(--sign-white); }
  .phone-number {
    font-family: "Arimo", Arial, sans-serif;
    font-weight: 700;
    font-size: 80px;
    fill: var(--sign-maroon);
  }
</style>
</head>
<body>
<svg class="sign-canvas" viewBox="0 0 1200 1000" xmlns="http://www.w3.org/2000/svg" role="img" aria-label="Meridale Commerce Park land for sale sign, build to suit, General and Limited Industrial zoning">
  <rect class="sign-panel" x="226" y="250" width="748" height="500"/>

  <g class="brand-lockup">
    <ellipse class="brand-oval" cx="600" cy="340" rx="340" ry="74"/>
    <text class="project-name" x="600" y="322" text-anchor="middle" letter-spacing="1">MERIDALE COMMERCE PARK</text>
    <rect class="brand-square" x="448" y="344" width="32" height="32"/>
    <text class="brand-name" x="494" y="368" textLength="340" lengthAdjust="spacingAndGlyphs">Brightline Property Partners, Inc.</text>
    <line class="brand-rule" x1="494" y1="378" x2="834" y2="378"/>
  </g>

  <text class="headline" x="600" y="522" text-anchor="middle" textLength="642" lengthAdjust="spacingAndGlyphs">LAND FOR SALE</text>
  <text class="zoning-line" x="600" y="590" text-anchor="middle" textLength="647" lengthAdjust="spacingAndGlyphs">GENERAL &amp; LIMITED INDUSTRIAL</text>
  <text class="offer-line" x="600" y="645" text-anchor="middle">BUILD TO SUIT  •  GI - LI</text>

  <rect class="phone-band" x="229" y="656" width="742" height="84"/>
  <text class="phone-number" x="602" y="725" text-anchor="middle" textLength="566" lengthAdjust="spacingAndGlyphs">415-736-2958</text>
</svg>
</body>
</html>
```